Printer Cartridges Supplier Namecard

Attached is my company logo and the design of my current namecard. I would like to have a more special look for it. Can have a little cuteness too rather than those normal standard feel. I'm a supplier mainly dealing with original and compatible printer toner cartridges, some other products like paper supplies as well.

Target Market(s)

Companies, businesses, corporates

Industry/Entity Type

It Company

Contact Information for Business Card

Logo, name, contact, address, supplies and maybe a slogan

Colors
85cae6
33a6d7
3176b5
0255a3
0792cd
85abd2

Requirements
Must have
• Logo, name, contact and address basic details.
• Must include some pictures, not just rearrange what I'm currently having.
Nice to have
• Be creative and bold, a diiferent traditional feel.

```html
<!DOCTYPE html>
<html lang="en">
<head>
<meta charset="utf-8">
<title>Tonerbay Namecard</title>
<link href="https://fonts.googleapis.com/css2?family=Roboto:wght@400&family=Work+Sans:wght@400;500&display=swap" rel="stylesheet">
<style>
  :root {
    --page-bg: #1c1c1c;
    --card-white: #ffffff;
    --brand-blue: #2a78bd;
    --pattern-blue: #3584c6;
    --pattern-soft: #3a8bcc;
    --accent-blue: #4aa8dd;
    --sky-blue: #5db5e5;
    --text-dark: #3a3a3a;
    --text-grey: #555555;
    --white: #ffffff;
  }
  * { margin: 0; padding: 0; box-sizing: border-box; }
  html, body { width: 1200px; height: 897px; overflow: hidden; }
  body {
    background: var(--page-bg);
    position: relative;
    font-family: "Work Sans", sans-serif;
  }
  .card {
    position: absolute;
    left: 303px;
    width: 595px;
    height: 338px;
    border-radius: 19px;
    overflow: hidden;
  }
  .card--front { top: 92px; background: var(--card-white); }
  .card--back { top: 469px; background: var(--brand-blue); }

  .back-pattern {
    position: absolute;
    inset: 0;
    background:
      radial-gradient(ellipse at 20% 25%, var(--pattern-soft) 0%, transparent 55%),
      radial-gradient(ellipse at 80% 75%, var(--pattern-soft) 0%, transparent 55%),
      linear-gradient(135deg, var(--pattern-blue) 0%, var(--brand-blue) 50%, var(--pattern-blue) 100%);
  }

  .brand {
    position: absolute;
    display: flex;
    align-items: center;
    gap: 12px;
  }
  .brand__mark {
    width: 34px; height: 34px;
    border-radius: 50%;
    background: var(--sky-blue);
    flex: none;
  }
  .brand__name {
    font-family: "Work Sans", sans-serif;
    font-weight: 500;
    font-size: 50px;
    line-height: 1;
    letter-spacing: -1px;
  }
  .brand__tagline {
    font-size: 8.5px;
    margin-top: 3px;
  }
  .card--front .brand { right: 38px; top: 44px; }
  .card--front .brand__name { color: var(--text-grey); }
  .card--front .brand__tagline { color: var(--text-grey); }

  .card--back .brand { left: 50%; top: 132px; transform: translateX(-50%); }
  .card--back .brand__mark { width: 44px; height: 44px; }
  .card--back .brand__name { color: var(--white); font-size: 60px; }
  .card--back .brand__tagline { color: var(--white); font-size: 10px; }

  .holder { position: absolute; left: 32px; top: 182px; }
  .holder__name {
    font-family: "Roboto", sans-serif;
    font-size: 19px;
    color: var(--accent-blue);
    letter-spacing: 0.2px;
  }
  .holder__role {
    font-size: 14px;
    color: var(--text-dark);
    letter-spacing: 0.6px;
    margin-top: 1px;
  }
  .divider {
    position: absolute;
    left: 32px; right: 38px; top: 232px;
    height: 2px;
    background: var(--accent-blue);
  }
  .contacts {
    position: absolute; left: 32px; top: 246px;
    list-style: none;
    font-size: 13.5px;
    color: var(--text-dark);
    line-height: 17.5px;
  }
  .contacts li { display: flex; align-items: center; gap: 9px; }
  .contacts svg { width: 8px; height: 8px; flex: none; }
  .address {
    position: absolute; right: 36px; top: 246px;
    text-align: right;
    font-size: 13.5px;
    line-height: 19px;
    color: var(--text-dark);
  }
  .footer-band { position: absolute; left: 0; bottom: 0; width: 595px; height: 30px; }
  .hotline {
    position: absolute; right: 36px; bottom: 6px;
    font-size: 13px;
    color: var(--white);
    letter-spacing: 0.8px;
  }
  .website {
    position: absolute; left: 0; right: 0; top: 298px;
    text-align: center;
    font-size: 13.5px;
    color: var(--white);
  }
</style>
</head>
<body>

<section class="card card--front">
  <div class="brand">
    <span class="brand__mark"></span>
    <div>
      <div class="brand__name">tonerbay</div>
      <div class="brand__tagline">Compatible printer ink and toner solutions</div>
    </div>
  </div>

  <div class="holder">
    <div class="holder__name">MIRA TAN</div>
    <div class="holder__role">Sales Executive</div>
  </div>
  <div class="divider"></div>

  <ul class="contacts">
    <li>
      <svg viewBox="0 0 10 10"><path d="M2 1 L4 1 L4.6 3.2 L3.4 4 Q4.4 6 6 6.8 L7 5.6 L9 6.2 L9 8.2 Q4 8.6 1.6 3 Z" fill="var(--accent-blue)"/></svg>
      912-555-0148
    </li>
    <li>
      <svg viewBox="0 0 10 10"><rect x="0.8" y="2" width="8.4" height="6" fill="none" stroke="var(--accent-blue)" stroke-width="1.2"/><path d="M0.8 2 L5 5.4 L9.2 2" fill="none" stroke="var(--accent-blue)" stroke-width="1.2"/></svg>
      mira@tonerbay.sg
    </li>
    <li>
      <svg viewBox="0 0 10 10"><circle cx="5" cy="5" r="4" fill="none" stroke="var(--accent-blue)" stroke-width="1"/><path d="M1 5 H9 M5 1 Q2.5 5 5 9 M5 1 Q7.5 5 5 9" fill="none" stroke="var(--accent-blue)" stroke-width="0.8"/></svg>
      www.tonerbay.sg
    </li>
  </ul>

  <div class="address">174A Riverside Walk<br>05-112 Singapore 530174</div>

  <svg class="footer-band" viewBox="0 0 595 30" preserveAspectRatio="none" aria-hidden="true">
    <path d="M0 8 H345 Q355 8 345 13 H0 Z" fill="var(--accent-blue)"/>
    <path d="M0 15 H342 Q370 2 385 0 H595 V30 H0 Z" fill="var(--brand-blue)"/>
  </svg>
  <div class="hotline">HP 8100 4471</div>
</section>

<section class="card card--back">
  <div class="back-pattern" role="img" aria-label="Repeating pattern of small printer icons in a lighter blue across the whole card"></div>
  <div class="brand">
    <span class="brand__mark"></span>
    <div>
      <div class="brand__name">tonerbay</div>
      <div class="brand__tagline">Compatible printer ink and toner solutions</div>
    </div>
  </div>
  <div class="website">www.tonerbay.sg</div>
</section>

</body>
</html>
```